Brand new redesign of Brightpath finance website

I need a new website design that i can advertise a great low interest rate on the front page and capture input application details that will send through to my email address.

some car finance companies will be similar to this would be listed below

tallowcredit.example.com.au
mirabelfinance.example.com.au
finance725.example.com.au
quenbyfinance.example.com.au
finance91.example.com.au

Reason: I have changed the project to a committed project. all the webpages should have the same format just different content and i want to be able to edit the front page easily to update my interest rates.

Target Market(s)

Australian Finance market targeting a younger demographic

Industry/Entity Type

Finance

Coding

Coded - Design and coding required

Number of Pages Required

5+ page

Font styles to use
Serif
Sans Serif

Colors
0255a3
ffffff
cedeed

Requirements
Must have
• application capture form
• apply now buttons
• Headline rate front page

```html
<!DOCTYPE html>
<html lang="en">
<head>
<meta charset="utf-8">
<title>Brightpath Finance</title>
<link href="https://fonts.googleapis.com/css2?family=Lato:wght@400;700;900&family=Signika:wght@400;600&display=swap" rel="stylesheet">
<style>
:root{
  --brand:#0255a3;
  --brand-dark:#0a4a8e;
  --white:#ffffff;
  --pale:#cedeed;
  --header:#231f20;
  --ink:#222222;
  --text:#333333;
  --field:#eeeeee;
  --field-line:#dddddd;
  --btn:#4a4a4a;
}
*{box-sizing:border-box;margin:0;padding:0}
html,body{width:813px;height:1200px;overflow:hidden;background:var(--white)}
body{position:relative;font-family:'Lato',sans-serif;color:var(--text)}
.abs{position:absolute}
.heading{font-family:'Signika',sans-serif;font-weight:600;text-transform:uppercase}

/* header */
.top-strip{left:0;top:0;width:813px;height:22px;background:var(--brand)}
.apply-tab{left:641px;top:0;width:83px;height:22px;background:#e9eef4;color:var(--brand);font-size:8.5px;display:flex;align-items:center;justify-content:center;gap:5px}
.masthead{left:0;top:22px;width:813px;height:80px;background:var(--header)}
.brand-name{left:88px;top:60px;width:120px;font-family:'Lato',sans-serif;font-weight:700;font-size:13px;line-height:15px;color:var(--brand);display:flex;align-items:center;gap:6px;letter-spacing:.3px}
.brand-name .dot{width:12px;height:12px;border-radius:50%;background:var(--brand);flex:none}
.phone{left:557px;top:42px;color:#dddddd;font-size:10px;display:flex;align-items:center;gap:5px}
.social{top:40px;width:18px;height:18px;background:var(--brand);border-radius:2px}
.main-nav{left:226px;top:72px;display:flex;gap:0;font-family:'Lato',sans-serif;font-weight:900;font-size:8.2px;color:var(--white)}
.main-nav span{padding:5px 10px;letter-spacing:.2px}
.main-nav .active{background:var(--brand)}

/* hero */
.hero{left:0;top:102px;width:813px;height:317px;background:linear-gradient(180deg,#5f93c9 0%,#3b72ad 45%,#12386a 100%)}
.hero-tag{left:90px;width:228px;background:rgba(20,22,30,.72);color:var(--white);font-size:11.5px;font-weight:700;padding:0 11px;display:flex;flex-direction:column;justify-content:center;line-height:1.4;border-radius:2px}
.slider-dot{top:399px;width:5px;height:5px;border-radius:50%;background:var(--white)}
.quote-form{left:514px;top:128px;width:210px;height:267px;background:var(--white);border-radius:2px}
.quote-form .form-title{height:32px;background:var(--brand);color:var(--white);font-family:'Signika',sans-serif;font-weight:600;font-size:14px;padding:8px 8px;letter-spacing:.2px}
.quote-form label{display:block;font-size:7.5px;color:#555;margin:10px 8px 5px}
.quote-form .field{margin:0 8px;height:22px;background:var(--field);border:1px solid var(--field-line);font-size:8px;padding:5px 6px;color:#333;position:relative}
.quote-form .field .caret{position:absolute;right:8px;top:8px;border-left:5px solid transparent;border-right:5px solid transparent;border-top:5px solid #444}
.submit{margin:15px 8px 0;width:70px;height:22px;background:var(--btn);color:var(--white);font-family:'Signika',sans-serif;font-weight:600;font-size:10.5px;display:flex;align-items:center;justify-content:center;border-radius:2px}

/* intro */
.intro-title{left:90px;top:442px;color:var(--brand);font-size:19px;letter-spacing:.4px}
.intro-rule{left:90px;top:469px;width:306px;height:1px;background:#c9d6e4}
.intro-copy{left:90px;top:484px;width:310px;font-size:8.6px;line-height:14.2px;color:#444}
.intro-copy strong{display:block;margin-top:6px;color:#222}
.intro-cta{left:90px;top:612px;font-size:11.5px;color:#333}
.intro-cta b{color:var(--brand);font-size:13px;margin-left:3px}
.loan-tile{width:141px;height:87px;background:var(--brand);color:var(--white);display:flex;flex-direction:column;align-items:center;justify-content:flex-end;padding-bottom:9px;font-family:'Signika',sans-serif;font-weight:600;font-size:11px;letter-spacing:.4px}
.loan-tile svg{margin-bottom:7px}

/* promos */
.promo{top:656px;width:407px;height:202px;color:var(--white);text-align:center}
.promo-calc{left:0;background:linear-gradient(135deg,#4d86c4 0%,#2f6fb3 55%,#1d5aa0 100%)}
.promo-approval{left:406px;width:407px;background:linear-gradient(135deg,#5a5650 0%,#3e3b38 50%,#2b2a2a 100%)}
.promo h2{font-family:'Signika',sans-serif;font-weight:600;font-size:16.5px;line-height:23px;letter-spacing:.5px;text-transform:uppercase}
.promo p{font-size:11px;line-height:16.5px;margin-top:8px}
.pill{display:inline-flex;align-items:center;gap:8px;background:rgba(255,255,255,.92);color:var(--brand);font-weight:700;font-size:10px;border-radius:14px;height:23px;padding:0 11px 0 4px;margin-top:10px}
.pill i{width:17px;height:17px;border-radius:50%;background:var(--brand);display:block;opacity:.7}

/* solutions */
.solutions-title{left:0;width:813px;top:879px;text-align:center;color:var(--brand);font-size:19px;letter-spacing:.5px}
.solutions-rule{left:253px;top:912px;width:306px;height:1px;background:#c9d6e4}
.solutions-list{left:378px;font-family:'Signika',sans-serif;font-weight:600;font-size:11px;color:#222;letter-spacing:.5px}

/* contact band */
.contact-band{left:0;top:1051px;width:813px;height:93px;background:var(--pale)}
.contact-item{top:1081px;display:flex;gap:10px}
.contact-item .badge{width:23px;height:23px;border-radius:50%;background:var(--brand);display:flex;align-items:center;justify-content:center;flex:none;margin-top:2px}
.contact-item h3{font-size:10px;font-weight:700;color:#222;margin-bottom:5px}
.contact-item p{font-size:10px;color:#333}
.contact-divider{top:1073px;width:1px;height:60px;background:var(--white)}

/* footer */
.site-footer{left:0;top:1144px;width:813px;height:56px;background:var(--brand)}
.footer-nav{left:90px;top:1157px;display:flex;gap:11px;font-size:7.6px;font-weight:700;color:var(--white);letter-spacing:.4px}
.copyright{left:90px;top:1175px;font-size:7.2px;font-weight:700;color:var(--white);letter-spacing:.3px}
.footer-social{top:1162px;width:17px;height:17px;background:#3f82c8;border-radius:2px}
</style>
</head>
<body>

<header>
  <div class="abs top-strip"></div>
  <div class="abs apply-tab">
    <svg width="9" height="11" viewBox="0 0 9 11"><path d="M1 .5h5l2.5 2.5v7.5H1z" fill="none" stroke="#333"/><path d="M2.5 5h4M2.5 7h4" stroke="#333"/></svg>
    Apply Now
  </div>
  <div class="abs masthead"></div>
  <div class="abs brand-name"><span class="dot"></span><span>BRIGHTPATH<br>FINANCE</span></div>
  <div class="abs phone">
    <svg width="13" height="13" viewBox="0 0 24 24"><path d="M6.6 10.8a15 15 0 006.6 6.6l2.2-2.2c.3-.3.7-.4 1-.2 1.1.4 2.3.6 3.6.6.6 0 1 .4 1 1V20c0 .6-.4 1-1 1A17 17 0 013 4c0-.6.4-1 1-1h3.5c.6 0 1 .4 1 1 0 1.200.2 2.4.6 3.6.1.3 0 .7-.2 1z" fill="none" stroke="#ccc" stroke-width="1.5"/></svg>
    1300 555 019
  </div>
  <div class="abs social" style="left:656px"></div>
  <div class="abs social" style="left:681px"></div>
  <div class="abs social" style="left:706px"></div>
  <nav class="abs main-nav">
    <span class="active">HOME</span><span>ABOUT</span><span>VEHICLE LOANS</span><span>OTHER LOANS</span><span>INSURANCE</span><span>FINANCE CALCULATOR</span><span>CONTACT</span>
  </nav>
</header>

<section>
  <div class="abs hero" role="img" aria-label="Photo of a white luxury motor yacht cruising on deep blue sea under a pale sky"></div>
  <div class="abs hero-tag" style="top:256px;height:38px">LOW RATE CAR LOANS FROM 4.69%<br>COMPARISON RATE 4.99%</div>
  <div class="abs hero-tag" style="top:306px;height:39px">LOW FEES</div>
  <div class="abs hero-tag" style="top:358px;height:38px">LOW TOTAL COST LOANS</div>
  <div class="abs slider-dot" style="left:385px"></div>
  <div class="abs slider-dot" style="left:398px;background:#2a6fc0"></div>
  <div class="abs slider-dot" style="left:411px"></div>
  <div class="abs slider-dot" style="left:424px"></div>

  <form class="abs quote-form">
    <div class="form-title">LET'S GET STARTED NOW!</div>
    <label>Loan Amount</label><div class="field"></div>
    <label>Deposit (if Any)</label><div class="field"></div>
    <label>Purpose of Loan</label><div class="field">Car<span class="caret"></span></div>
    <label>Postal Code</label><div class="field"></div>
    <div class="submit">SUBMIT</div>
  </form>
</section>

<section>
  <h1 class="abs heading intro-title">Online Loan Pre Approval</h1>
  <div class="abs intro-rule"></div>
  <div class="abs intro-copy">
    Lorem ipsum dolor sit amet, consectetuer adipiscing elit, sed dia nonummy laoreet dolore magna aliquam erat volutpat. Ut wisi enim ad minim veniam, quis nostrud exerci tation ullamcorper suscipit lobortis nisl ut aliquip ex eaLorem ipsum dolor sit amet, consectetuer adipiscing elit, sed dia nonummy laoreet dolore magna aliquam erat volutpat. Ut wisi enim ad minim veniam, quis nostrud exerci tation ullamcorper suscipit lobortis
    <strong>Lorem ipsum dolor sit amet, consectetuer adipiscing elit, sed dia nonummy laoreet dolore magna aliquam erat volutpat.</strong>
  </div>
  <div class="abs intro-cta">Fill Out Our Quick Form Below or <b>Call 1300 555 019</b></div>

  <div class="abs loan-tile" style="left:429px;top:446px">
    <svg width="42" height="42" viewBox="0 0 42 42"><circle cx="21" cy="21" r="20" fill="#fff"/><path d="M11 25v-4l3-6h14l3 6v4z" fill="var(--brand)"/><circle cx="15" cy="27" r="2.5" fill="var(--brand)"/><circle cx="27" cy="27" r="2.5" fill="var(--brand)"/></svg>
    VEHICLE LOANS
  </div>
  <div class="abs loan-tile" style="left:582px;top:446px">
    <svg width="42" height="42" viewBox="0 0 42 42"><circle cx="21" cy="21" r="20" fill="#fff"/><path d="M10 23h22l-4 6H14z" fill="var(--brand)"/><path d="M15 22v-5h12v5z" fill="var(--brand)"/><path d="M19 17v-4h4v4" fill="var(--brand)"/></svg>
    BOAT LOANS
  </div>
  <div class="abs loan-tile" style="left:429px;top:544px">
    <svg width="42" height="42" viewBox="0 0 42 42"><circle cx="21" cy="21" r="20" fill="#fff"/><path d="M9 21l12-10 12 10h-4v9h-5v-6h-6v6h-5v-9z" fill="var(--brand)"/></svg>
    HOME LOANS
  </div>
  <div class="abs loan-tile" style="left:582px;top:544px">
    <svg width="42" height="42" viewBox="0 0 42 42"><circle cx="21" cy="21" r="20" fill="#fff"/><circle cx="21" cy="16" r="4" fill="var(--brand)"/><path d="M13 30v-4c0-3 3-5 8-5s8 2 8 5v4z" fill="var(--brand)"/></svg>
    PERSONAL LOANS
  </div>
</section>

<section>
  <div class="abs promo promo-calc" role="img" aria-label="Blue-tinted photo of a hand using a calculator on paperwork"></div>
  <div class="abs promo" style="left:0;padding-top:38px">
    <h2>What Will<br>My Repayments Be?</h2>
    <p>See How Much You Could Borrow With<br>Our Loan Calculator</p>
    <span class="pill"><i></i>LOAN CALCULATOR</span>
  </div>
  <div class="abs promo promo-approval" role="img" aria-label="Photo of a smiling young driver leaning on a dark car"></div>
  <div class="abs promo" style="left:406px;padding-top:44px">
    <h2>Find Out What Guaranteed<br>Approval Actually Means</h2>
    <p>We Explain What it Means and<br>What We Offer Instead</p>
    <span class="pill" style="padding-right:16px"><i></i>&nbsp;&nbsp;&nbsp;FIND OUT MORE</span>
  </div>
</section>

<section>
  <h2 class="abs heading solutions-title">Brightpath Solutions</h2>
  <div class="abs solutions-rule"></div>
  <svg class="abs" style="left:210px;top:935px" width="170" height="95" viewBox="0 0 170 95">
    <circle cx="48" cy="47" r="42" fill="none" stroke="var(--brand)" stroke-width="3"/>
    <g stroke="#3a9ad9" stroke-width=".8" stroke-dasharray="2 2" fill="none">
      <path d="M95 45L160 11M95 47L160 35M95 49L160 60M95 51L160 86"/>
    </g>
    <g fill="#3a9ad9"><circle cx="162" cy="11" r="1.8"/><circle cx="162" cy="35" r="1.8"/><circle cx="162" cy="60" r="1.8"/><circle cx="162" cy="86" r="1.8"/></g>
  </svg>
  <div class="abs solutions-list" style="top:939px">BAS AGENT</div>
  <div class="abs solutions-list" style="top:964px">PAYROLL AND BOOKKEEPING SERVICES</div>
  <div class="abs solutions-list" style="top:989px">CREDIT FILE REPAIR / DEFAULT REMOVALS</div>
  <div class="abs solutions-list" style="top:1014px">DEBT CONSOLIDATION</div>
</section>

<section>
  <div class="abs contact-band"></div>
  <div class="abs contact-item" style="left:90px">
    <span class="badge"><svg width="10" height="13" viewBox="0 0 10 13"><path d="M5 0a5 5 0 015 5c0 3.5-5 8-5 8S0 8.5 0 5a5 5 0 015-5z" fill="#fff"/><circle cx="5" cy="5" r="1.8" fill="var(--brand)"/></svg></span>
    <div><h3>BRIGHTPATH FINANCE</h3><p>48 Harbour Row, Kelsey Bay - 204519</p></div>
  </div>
  <div class="abs contact-divider" style="left:354px"></div>
  <div class="abs contact-item" style="left:394px">
    <span class="badge"><svg width="12" height="12" viewBox="0 0 24 24"><path d="M6.6 10.8a15 15 0 006.6 6.6l2.2-2.2c.3-.3.7-.4 1-.2 1.1.4 2.3.6 3.6.6.6 0 1 .4 1 1V20c0 .6-.4 1-1 1A17 17 0 013 4c0-.6.4-1 1-1h3.5c.6 0 1 .4 1 1 0 1.2.2 2.4.6 3.6.1.3 0 .7-.2 1z" fill="#fff"/></svg></span>
    <div><h3>CALL US</h3><p>1300 555 019</p></div>
  </div>
  <div class="abs contact-divider" style="left:532px"></div>
  <div class="abs contact-item" style="left:571px">
    <span class="badge"><svg width="12" height="9" viewBox="0 0 12 9"><rect width="12" height="9" rx="1" fill="#fff"/><path d="M.5 .8L6 5l5.5-4.2" fill="none" stroke="var(--brand)"/></svg></span>
    <div><h3>EMAIL US</h3><p>info@brightpathfinance.example.com</p></div>
  </div>
</section>

<footer>
  <div class="abs site-footer"></div>
  <nav class="abs footer-nav"><span>HOME</span><span>ABOUT</span><span>VEHICLE LOANS</span><span>OTHER LOANS</span><span>INSURANCE</span><span>FINANCE CALCULATOR</span><span>CONTACT</span></nav>
  <div class="abs copyright">COPYRIGHT © 2016 BRIGHTPATH FINANCE. ALL RIGHTS RESERVED.</div>
  <div class="abs footer-social" style="left:656px"></div>
  <div class="abs footer-social" style="left:681px"></div>
  <div class="abs footer-social" style="left:706px"></div>
</footer>

</body>
</html>
```